Spring Detox sale graphics for social media

You MUST read the Brief in the WORD document and follow the instructions there. I want to create 10 social media graphics (new Instagram size 4:5 (1080 x 1350 pixels) focusing on our Mother’s Day Spring Detox Sale graphics, using any of the pics attached. Use the attached pics, NO RANDOM STOCK PHOTOGRAPHY. For the color scheme of the graphics, they should all be complementary to the product colors or feel like Spring time.

Target Market(s)

primarily women

Requirements
Must have
• the photos and text attached

```html
<!DOCTYPE html>
<html lang="en">
<head>
<meta charset="utf-8">
<title>Mother's Day Spring Detox Sale – Social Set</title>
<link href="https://fonts.googleapis.com/css2?family=Oswald:wght@500;600;700&family=Nunito:wght@800&display=swap" rel="stylesheet">
<style>
:root{
  --ink-black:#000;
  --leaf-green:#245c2e;
  --deep-green:#1d3a22;
  --blossom-pink:#e0509a;
  --plum-gray:#4a3b40;
  --cherry-red:#d11c35;
  --navy:#0a0f9a;
  --cream:#fdf3ec;
  --blush:#f8eaee;
  --mint:#ecfbf0;
  --mint-frame:#d6fbd8;
  --white:#fff;
}
*{margin:0;padding:0;box-sizing:border-box}
html,body{width:1200px;height:2652px;overflow:hidden;background:var(--ink-black)}
.board{position:relative;width:1200px;height:2652px}
.defs{position:absolute;width:0;height:0}
.post{position:absolute;width:344px;height:430px;display:block;overflow:hidden}
.col-a{left:248px}.col-b{left:607px}
.row-1{top:215px}.row-2{top:663px}.row-3{top:1110px}.row-4{top:1557px}.row-5{top:2005px}
.hd{font-family:"Oswald",sans-serif;font-weight:600;letter-spacing:0}
.hd-light{font-family:"Oswald",sans-serif;font-weight:500}
.hd-heavy{font-family:"Oswald",sans-serif;font-weight:700}
.tag{font-family:"Nunito",sans-serif;font-weight:800}
.green{fill:var(--leaf-green)}.pink{fill:var(--blossom-pink)}.plum{fill:var(--plum-gray)}
.red{fill:var(--cherry-red)}.navy{fill:var(--navy)}.deep{fill:var(--deep-green)}.cream{fill:var(--cream)}
</style>
</head>
<body>
<main class="board">

  <svg class="defs" aria-hidden="true">
    <defs>
      <linearGradient id="bottle-shade" x1="0" x2="1" y1="0" y2="0">
        <stop offset="0" stop-color="#d6d6d6"/><stop offset=".35" stop-color="#fff"/>
        <stop offset=".7" stop-color="#f1f1f1"/><stop offset="1" stop-color="#cbcbcb"/>
      </linearGradient>
      <linearGradient id="watercolor-wash" x1="0" x2="1" y1="0" y2="1">
        <stop offset="0" stop-color="#fff6ef"/><stop offset="1" stop-color="#fde6de"/>
      </linearGradient>
      <radialGradient id="floral-frame" cx=".5" cy=".5" r=".7">
        <stop offset=".55" stop-color="#fff6ef" stop-opacity="0"/>
        <stop offset=".82" stop-color="#f4b9c2" stop-opacity=".6"/>
        <stop offset="1" stop-color="#b9d79a" stop-opacity=".6"/>
      </radialGradient>
      <radialGradient id="foliage-tr" cx="1" cy="0" r="1">
        <stop offset="0" stop-color="#245c2e" stop-opacity=".8"/>
        <stop offset=".5" stop-color="#e0509a" stop-opacity=".35"/>
        <stop offset="1" stop-color="#f6e6ee" stop-opacity="0"/>
      </radialGradient>
      <radialGradient id="foliage-bl" cx="0" cy="1" r="1">
        <stop offset="0" stop-color="#245c2e" stop-opacity=".8"/>
        <stop offset=".5" stop-color="#e0509a" stop-opacity=".35"/>
        <stop offset="1" stop-color="#f6e6ee" stop-opacity="0"/>
      </radialGradient>
      <radialGradient id="blossom-branch" cx="1" cy="0" r="1">
        <stop offset="0" stop-color="#e896aa" stop-opacity=".85"/>
        <stop offset="1" stop-color="#e896aa" stop-opacity="0"/>
      </radialGradient>
      <linearGradient id="studio-gray" x1="0" x2="0" y1="0" y2="1">
        <stop offset="0" stop-color="#ebe9eb"/><stop offset="1" stop-color="#cfcdd0"/>
      </linearGradient>
      <linearGradient id="lilac-blush" x1="0" x2="0" y1="0" y2="1">
        <stop offset="0" stop-color="#eeeafc"/><stop offset="1" stop-color="#fbe9ee"/>
      </linearGradient>
      <linearGradient id="portrait-tone" x1="0" x2="0" y1="0" y2="1">
        <stop offset="0" stop-color="#ece6e2"/><stop offset="1" stop-color="#d8d1cd"/>
      </linearGradient>
    </defs>
  </svg>

  <!-- 1 -->
  <svg class="post col-a row-1" viewBox="0 0 344 430">
    <rect width="344" height="430" fill="url(#watercolor-wash)"/>
    <rect width="344" height="430" fill="url(#floral-frame)" role="img" aria-label="Watercolor pink blossoms and green leaves framing the edges"/>
    <text class="hd green" x="59" y="123" font-size="44" textLength="218" lengthAdjust="spacingAndGlyphs">MOTHER’S DAY</text>
    <text class="hd pink" x="59" y="205" font-size="89" textLength="219" lengthAdjust="spacingAndGlyphs">SPRING</text>
    <text class="hd pink" x="59" y="262" font-size="57" textLength="221" lengthAdjust="spacingAndGlyphs">DETOX SALE</text>
    <text class="hd green" x="59" y="340" font-size="83" textLength="76" lengthAdjust="spacingAndGlyphs">25</text>
    <text class="hd green" x="143" y="300" font-size="34" textLength="33" lengthAdjust="spacingAndGlyphs">%</text>
    <text class="hd green" x="142" y="340" font-size="28" textLength="40" lengthAdjust="spacingAndGlyphs">OFF</text>
    <text class="tag plum" x="192" y="312" font-size="16" textLength="90" lengthAdjust="spacingAndGlyphs">Everything!</text>
  </svg>

  <!-- 2 -->
  <svg class="post col-b row-1" viewBox="0 0 344 430">
    <rect width="344" height="430" fill="#f6e6ee"/>
    <rect x="140" y="0" width="204" height="210" fill="url(#foliage-tr)" role="img" aria-label="Tropical leaves, berries and pink flowers in the top right corner"/>
    <rect x="0" y="230" width="190" height="200" fill="url(#foliage-bl)" role="img" aria-label="Tropical leaves, berries and pink flowers in the bottom left corner"/>
    <text class="hd green" x="61" y="128" font-size="83" textLength="80" lengthAdjust="spacingAndGlyphs">25</text>
    <text class="hd green" x="148" y="90" font-size="40" textLength="35" lengthAdjust="spacingAndGlyphs">%</text>
    <text class="hd green" x="148" y="128" font-size="30" textLength="40" lengthAdjust="spacingAndGlyphs">OFF</text>
    <text class="hd green" x="61" y="183" font-size="44" textLength="227" lengthAdjust="spacingAndGlyphs">MOTHER’S DAY</text>
    <text class="hd pink" x="61" y="267" font-size="90" textLength="227" lengthAdjust="spacingAndGlyphs">SPRING</text>
    <text class="hd pink" x="61" y="328" font-size="60" textLength="229" lengthAdjust="spacingAndGlyphs">DETOX SALE</text>
  </svg>

  <!-- 3 -->
  <svg class="post col-a row-2" viewBox="0 0 344 430">
    <rect width="344" height="430" fill="var(--mint)"/>
    <text class="hd green" x="89" y="112" font-size="106" textLength="103" lengthAdjust="spacingAndGlyphs">25</text>
    <text class="hd green" x="199" y="62" font-size="50" textLength="45" lengthAdjust="spacingAndGlyphs">%</text>
    <text class="hd green" x="199" y="112" font-size="36" textLength="50" lengthAdjust="spacingAndGlyphs">OFF</text>
    <text class="tag green" x="58" y="137" font-size="26" textLength="224" lengthAdjust="spacingAndGlyphs">All Supplements</text>
    <text class="hd pink" x="58" y="227" font-size="88" textLength="219" lengthAdjust="spacingAndGlyphs">SPRING</text>
    <text class="hd pink" x="58" y="280" font-size="55" textLength="222" lengthAdjust="spacingAndGlyphs">DETOX SALE</text>
    <rect x="44" y="298" width="62" height="122" rx="9" fill="url(#bottle-shade)" role="img" aria-label="Liver support supplement bottle"/>
    <rect x="114" y="298" width="56" height="122" rx="9" fill="url(#bottle-shade)" role="img" aria-label="Digestive support supplement bottle"/>
    <rect x="178" y="298" width="56" height="122" rx="9" fill="url(#bottle-shade)" role="img" aria-label="Hormone support supplement bottle"/>
    <rect x="248" y="300" width="50" height="112" rx="9" fill="url(#bottle-shade)" role="img" aria-label="Blood sugar support supplement bottle"/>
  </svg>

  <!-- 4 -->
  <svg class="post col-b row-2" viewBox="0 0 344 430">
    <rect width="344" height="430" fill="var(--cream)"/>
    <rect x="0" y="0" width="180" height="300" fill="url(#portrait-tone)" role="img" aria-label="Smiling woman in a white cropped sweater"/>
    <rect x="0" y="300" width="190" height="130" fill="#e8e4e2" role="img" aria-label="Row of supplement and skincare bottles"/>
    <text class="hd green" x="188" y="87" font-size="76" textLength="85" lengthAdjust="spacingAndGlyphs">25</text>
    <text class="hd green" x="275" y="55" font-size="40" textLength="35" lengthAdjust="spacingAndGlyphs">%</text>
    <text class="hd green" x="275" y="87" font-size="26" textLength="40" lengthAdjust="spacingAndGlyphs">OFF</text>
    <text class="hd pink" x="185" y="147" font-size="51" textLength="125" lengthAdjust="spacingAndGlyphs">SPRING</text>
    <text class="hd pink" x="185" y="197" font-size="51" textLength="111" lengthAdjust="spacingAndGlyphs">DETOX</text>
    <text class="hd pink" x="185" y="242" font-size="51" textLength="85" lengthAdjust="spacingAndGlyphs">SALE</text>
    <text class="hd-light green" x="219" y="287" font-size="37" textLength="96" lengthAdjust="spacingAndGlyphs">Spring</text>
    <text class="hd-light green" x="219" y="323" font-size="37" textLength="81" lengthAdjust="spacingAndGlyphs">Reset</text>
    <text class="hd-light green" x="219" y="362" font-size="37" textLength="106" lengthAdjust="spacingAndGlyphs">Summer</text>
    <text class="hd-light green" x="219" y="395" font-size="37" textLength="76" lengthAdjust="spacingAndGlyphs">Ready</text>
  </svg>

  <!-- 5 -->
  <svg class="post col-a row-3" viewBox="0 0 344 430">
    <rect width="344" height="430" fill="url(#studio-gray)"/>
    <rect x="150" y="0" width="194" height="90" fill="url(#blossom-branch)" role="img" aria-label="Pink cherry blossom branch"/>
    <text class="hd plum" x="44" y="120" font-size="83" textLength="83" lengthAdjust="spacingAndGlyphs">25</text>
    <text class="hd plum" x="135" y="85" font-size="42" textLength="37" lengthAdjust="spacingAndGlyphs">%</text>
    <text class="hd plum" x="135" y="121" font-size="29" textLength="42" lengthAdjust="spacingAndGlyphs">OFF</text>
    <text class="tag plum" x="189" y="93" font-size="17" textLength="98" lengthAdjust="spacingAndGlyphs">Everything!</text>
    <text class="hd plum" x="47" y="173" font-size="46" textLength="237" lengthAdjust="spacingAndGlyphs">MOTHER’S DAY</text>
    <text class="hd red" x="47" y="260" font-size="95" textLength="237" lengthAdjust="spacingAndGlyphs">SPRING</text>
    <text class="hd red" x="47" y="315" font-size="57" textLength="240" lengthAdjust="spacingAndGlyphs">DETOX SALE</text>
    <rect x="110" y="340" width="36" height="72" rx="7" fill="url(#bottle-shade)" role="img" aria-label="Blood sugar support supplement bottle"/>
    <rect x="144" y="334" width="44" height="82" rx="8" fill="url(#bottle-shade)" role="img" aria-label="Hormone support supplement bottle"/>
    <rect x="186" y="328" width="50" height="92" rx="8" fill="url(#bottle-shade)" role="img" aria-label="Digestive support supplement bottle"/>
    <rect x="234" y="324" width="62" height="100" rx="9" fill="url(#bottle-shade)" role="img" aria-label="Liver support supplement bottle"/>
  </svg>

  <!-- 6 -->
  <svg class="post col-b row-3" viewBox="0 0 344 430">
    <rect width="344" height="430" fill="url(#lilac-blush)"/>
    <text class="hd-heavy deep" x="83" y="105" font-size="86" textLength="107" lengthAdjust="spacingAndGlyphs">25</text>
    <text class="hd-heavy deep" x="193" y="62" font-size="48" textLength="40" lengthAdjust="spacingAndGlyphs">%</text>
    <text class="hd-heavy deep" x="193" y="105" font-size="30" textLength="68" lengthAdjust="spacingAndGlyphs">OFF</text>
    <text class="hd-heavy navy" x="51" y="163" font-size="50" textLength="238" lengthAdjust="spacingAndGlyphs">MOTHER’S DAY</text>
    <text class="hd-heavy navy" x="58" y="275" font-size="128" textLength="217" lengthAdjust="spacingAndGlyphs">SALE</text>
    <text class="hd deep" x="33" y="332" font-size="54" textLength="278" lengthAdjust="spacingAndGlyphs">Feel Amazing</text>
    <text class="hd deep" x="103" y="395" font-size="54" textLength="135" lengthAdjust="spacingAndGlyphs">Again!</text>
  </svg>

  <!-- 7 -->
  <svg class="post col-a row-4" viewBox="0 0 344 430">
    <rect width="344" height="430" fill="var(--mint-frame)"/>
    <rect x="22" y="21" width="298" height="382" fill="var(--white)"/>
    <text class="hd-heavy pink" x="89" y="111" font-size="77" textLength="98" lengthAdjust="spacingAndGlyphs">25</text>
    <text class="hd-heavy pink" x="192" y="75" font-size="40" textLength="38" lengthAdjust="spacingAndGlyphs">%</text>
    <text class="hd-heavy pink" x="192" y="111" font-size="26" textLength="65" lengthAdjust="spacingAndGlyphs">OFF</text>
    <text class="hd green" x="43" y="203" font-size="79" textLength="257" lengthAdjust="spacingAndGlyphs">MOTHER’S</text>
    <text class="hd green" x="50" y="268" font-size="73" textLength="242" lengthAdjust="spacingAndGlyphs">DAY SALE</text>
    <text class="hd pink" x="77" y="328" font-size="55" textLength="192" lengthAdjust="spacingAndGlyphs">REFRESH</text>
    <text class="hd pink" x="44" y="388" font-size="61" textLength="260" lengthAdjust="spacingAndGlyphs">YOUR BODY</text>
  </svg>

  <!-- 8 -->
  <svg class="post col-b row-4" viewBox="0 0 344 430">
    <rect width="344" height="430" fill="var(--cream)"/>
    <text class="hd pink" x="18" y="98" font-size="67" textLength="312" lengthAdjust="spacingAndGlyphs">SPRING DETOX</text>
    <text class="hd pink" x="18" y="188" font-size="98" textLength="167" lengthAdjust="spacingAndGlyphs">SALE</text>
    <circle cx="278" cy="173" r="51" fill="var(--leaf-green)"/>
    <text class="hd cream" x="238" y="193" font-size="46" textLength="48" lengthAdjust="spacingAndGlyphs">25</text>
    <text class="hd cream" x="290" y="168" font-size="24" textLength="23" lengthAdjust="spacingAndGlyphs">%</text>
    <text class="hd cream" x="290" y="193" font-size="18" textLength="25" lengthAdjust="spacingAndGlyphs">OFF</text>
    <text class="hd-light green" x="18" y="235" font-size="39" textLength="213" lengthAdjust="spacingAndGlyphs">Spring Cleanse</text>
    <text class="hd-light green" x="18" y="285" font-size="39" textLength="195" lengthAdjust="spacingAndGlyphs">Summer Glow</text>
    <rect x="25" y="298" width="70" height="124" rx="10" fill="url(#bottle-shade)" role="img" aria-label="Liver support supplement bottle"/>
    <rect x="105" y="298" width="64" height="124" rx="10" fill="url(#bottle-shade)" role="img" aria-label="Digestive support supplement bottle"/>
    <rect x="180" y="298" width="64" height="124" rx="10" fill="url(#bottle-shade)" role="img" aria-label="Hormone support supplement bottle"/>
    <rect x="260" y="298" width="58" height="124" rx="10" fill="url(#bottle-shade)" role="img" aria-label="Blood sugar support supplement bottle"/>
  </svg>

  <!-- 9 -->
  <svg class="post col-a row-5" viewBox="0 0 344 430">
    <rect width="344" height="430" fill="var(--blush)"/>
    <path d="M230 0 H344 V198 C320 150 300 100 230 0 Z" class="green"/>
    <path d="M0 200 C40 280 90 380 135 430 H0 Z" class="green"/>
    <text class="hd green" x="60" y="125" font-size="83" textLength="82" lengthAdjust="spacingAndGlyphs">25</text>
    <text class="hd green" x="149" y="85" font-size="40" textLength="35" lengthAdjust="spacingAndGlyphs">%</text>
    <text class="hd green" x="149" y="127" font-size="29" textLength="40" lengthAdjust="spacingAndGlyphs">OFF</text>
    <text class="hd green" x="62" y="182" font-size="45" textLength="227" lengthAdjust="spacingAndGlyphs">MOTHER’S DAY</text>
    <text class="hd green" x="62" y="270" font-size="91" textLength="155" lengthAdjust="spacingAndGlyphs">SALE</text>
    <text class="hd-light pink" x="60" y="323" font-size="44" textLength="252" lengthAdjust="spacingAndGlyphs">DETOX THIS SPRING.</text>
    <text class="hd-light pink" x="60" y="365" font-size="44" textLength="258" lengthAdjust="spacingAndGlyphs">SHINE THIS SUMMER</text>
  </svg>

  <!-- 10 -->
  <svg class="post col-b row-5" viewBox="0 0 344 430">
    <rect width="344" height="430" fill="var(--blush)"/>
    <rect x="172" y="32" width="34" height="70" rx="7" fill="url(#bottle-shade)" role="img" aria-label="Blood sugar support supplement bottle"/>
    <rect x="206" y="30" width="40" height="76" rx="7" fill="url(#bottle-shade)" role="img" aria-label="Hormone support supplement bottle"/>
    <rect x="246" y="27" width="44" height="82" rx="8" fill="url(#bottle-shade)" role="img" aria-label="Digestive support supplement bottle"/>
    <rect x="288" y="22" width="52" height="92" rx="8" fill="url(#bottle-shade)" role="img" aria-label="Liver support supplement bottle"/>
    <text class="hd green" x="35" y="138" font-size="83" textLength="80" lengthAdjust="spacingAndGlyphs">25</text>
    <text class="hd green" x="121" y="98" font-size="40" textLength="37" lengthAdjust="spacingAndGlyphs">%</text>
    <text class="hd green" x="121" y="140" font-size="29" textLength="40" lengthAdjust="spacingAndGlyphs">OFF</text>
    <text class="hd green" x="35" y="195" font-size="49" textLength="263" lengthAdjust="spacingAndGlyphs">MOTHER’S DAY</text>
    <text class="hd green" x="35" y="280" font-size="91" textLength="148" lengthAdjust="spacingAndGlyphs">SALE</text>
    <text class="hd pink" x="35" y="340" font-size="57" textLength="263" lengthAdjust="spacingAndGlyphs">SPRING DETOX</text>
    <text class="hd-light pink" x="35" y="385" font-size="37" textLength="263" lengthAdjust="spacingAndGlyphs">FOR A SUMMER BODY</text>
  </svg>

</main>
</body>
</html>
```